Hvac and insulation company needs good looking business card design

We are hvac and insulation company and looking for a new business cards that look to today standards designs

Target Market(s)

homeowners

Industry/Entity Type

Hvac

Contact Information for Business Card

Name: Walter Brinoku
Home comfort consultant
address: 4827 Dunmore St #215 Oakland, CA 94619
office: 888-316-2790
cell: 510-742-3185
Lic.# 584261
Email: walter@corvane-hvac.com
Web: corvane-hvac.com

Requirements
Must have
• clean and sleek look
Nice to have
• simple with a clean look
Should not have
• to busy business card

```html
<!DOCTYPE html>
<html lang="en">
<head>
<meta charset="UTF-8">
<title>Corvane Home Solutions – Business Card</title>
<link href="https://fonts.googleapis.com/css2?family=Open+Sans:wght@400;600;700&display=swap" rel="stylesheet">
<style>
  :root {
    --orange: #e8781f;
    --orange-deep: #c5621a;
    --band-grey: #6e6f71;
    --text-grey: #5b5c5e;
    --logo-grey: #d2d2d2;
    --card-white: #ffffff;
    --card-shade: #ececec;
    --backdrop: #e9e9ea;
  }
  * { box-sizing: border-box; margin: 0; padding: 0; }
  html, body { width: 1200px; height: 900px; overflow: hidden; }
  body {
    background: var(--backdrop);
    font-family: "Open Sans", Arial, sans-serif;
    position: relative;
  }
  .card {
    position: absolute;
    left: 280px;
    width: 640px;
    height: 366px;
    border-radius: 22px;
    overflow: hidden;
    box-shadow: 0 10px 28px rgba(0,0,0,0.18);
  }
  /* Front */
  .card-front {
    top: 60px;
    background: linear-gradient(160deg, var(--card-shade) 0%, var(--card-white) 45%, var(--card-white) 100%);
  }
  .name-band {
    position: absolute;
    left: 0; top: 34px;
    width: 360px; height: 70px;
    background: var(--band-grey);
    border-radius: 0 35px 35px 0;
    padding: 10px 0 0 36px;
    color: #fff;
  }
  .name-band .person-name {
    font-size: 25px; font-weight: 600; letter-spacing: 0.5px;
    text-transform: uppercase; line-height: 1.1;
  }
  .name-band .person-title {
    font-size: 15px; font-weight: 400; letter-spacing: 0.8px; margin-top: 2px;
  }
  .brand-front {
    position: absolute;
    left: 380px; top: 44px;
    display: flex; align-items: center; gap: 10px;
    color: var(--orange);
  }
  .brand-mark {
    width: 14px; height: 14px; background: var(--orange);
  }
  .brand-name {
    font-size: 22px; font-weight: 700; line-height: 1.1;
  }
  .contact-list {
    position: absolute;
    left: 36px; top: 178px;
    list-style: none;
    color: var(--text-grey);
    font-size: 17px; line-height: 27px;
  }
  .contact-list li { display: flex; align-items: center; gap: 10px; }
  .contact-list svg { width: 13px; height: 13px; fill: var(--orange); flex-shrink: 0; }
  .contact-list .web-domain { color: var(--orange); }
  .address {
    position: absolute;
    right: 36px; bottom: 34px;
    text-align: right;
    color: var(--text-grey);
    font-size: 17px; line-height: 25px;
  }
  /* Back */
  .card-back {
    top: 474px;
    background: linear-gradient(135deg, var(--orange) 0%, var(--orange-deep) 100%);
    display: flex; flex-direction: column; align-items: center; justify-content: center;
    gap: 34px;
  }
  .brand-back {
    display: flex; align-items: center; gap: 16px;
    color: var(--logo-grey);
  }
  .brand-back .brand-mark { width: 26px; height: 26px; background: var(--logo-grey); }
  .brand-back .brand-name { font-size: 44px; }
  .license {
    color: var(--logo-grey);
    font-size: 22px; font-weight: 600; letter-spacing: 1px;
  }
</style>
</head>
<body>
  <section class="card card-front">
    <div class="name-band">
      <p class="person-name">Walter Brinoku</p>
      <p class="person-title">Home comfort consultant</p>
    </div>
    <div class="brand-front">
      <span class="brand-mark"></span>
      <span class="brand-name">Corvane Home Solutions</span>
    </div>
    <ul class="contact-list">
      <li>
        <svg viewBox="0 0 16 16"><path d="M3 1l3 0 1.5 4-2 1.5a9 9 0 0 0 4 4L11 8.5l4 1.5v3a2 2 0 0 1-2 2A12 12 0 0 1 1 3a2 2 0 0 1 2-2z"/></svg>
        888-316-2790
      </li>
      <li>
        <svg viewBox="0 0 16 16"><path d="M4 0h8a1 1 0 0 1 1 1v14a1 1 0 0 1-1 1H4a1 1 0 0 1-1-1V1a1 1 0 0 1 1-1zm1 2v10h6V2zm3 11a1 1 0 1 0 0 2 1 1 0 0 0 0-2z"/></svg>
        510-742-3185
      </li>
      <li>
        <svg viewBox="0 0 16 16"><path d="M0 3h16v10H0zm1.5 1.2L8 9l6.5-4.8V4h-13z"/></svg>
        walter@corvane-hvac.com
      </li>
      <li>
        <svg viewBox="0 0 16 16"><path d="M8 0a8 8 0 1 0 0 16A8 8 0 0 0 8 0zm0 1.5c.9 0 2 2 2.3 5.5H5.7C6 3.5 7.1 1.5 8 1.5zM1.6 9h2.6c.1 2 .6 3.8 1.3 4.9A6.5 6.5 0 0 1 1.6 9zm0-2a6.5 6.5 0 0 1 3.9-4.9C4.8 3.2 4.3 5 4.2 7zm6.4 7.5c-.9 0-2-2-2.3-5.5h4.6c-.3 3.5-1.4 5.5-2.3 5.5zm2.5-.6c.7-1.1 1.2-2.9 1.3-4.9h2.6a6.5 6.5 0 0 1-3.9 4.9zM11.8 7c-.1-2-.6-3.8-1.3-4.9A6.5 6.5 0 0 1 14.4 7z"/></svg>
        <span>www.<span class="web-domain">corvane-hvac</span>.com</span>
      </li>
    </ul>
    <address class="address" style="font-style: normal;">
      4827 Dunmore St<br>
      #215 Oakland, CA 94619
    </address>
  </section>

  <section class="card card-back">
    <div class="brand-back">
      <span class="brand-mark"></span>
      <span class="brand-name">Corvane Home Solutions</span>
    </div>
    <p class="license">Lic.# 584261</p>
  </section>
</body>
</html>
```